Local Roofing/Construction company business needs new biz card design

We need a new business card design, current cards are from the start of this operation and generic at best. We are a local Construction Company (General Contractor) with a majority of our work originating from insurance claims-exterior finish work is the main focus (Roofs-Siding-Gutters etc). Heavily involved with homeowners and the low ball offers they receive from insurance company's after a insurable event takes place. I have attached some of our original logo file(s) below.

```html
<!DOCTYPE html>
<html lang="en">
<head>
<meta charset="utf-8">
<title>Tallbrook Construction — Business Card</title>
<link href="https://fonts.googleapis.com/css2?family=Exo+2:wght@400;700;800&display=swap" rel="stylesheet">
<style>
  :root {
    --bg: #1c1c1c;
    --green: #31d67b;
    --green-deep: #2bc470;
    --white: #ffffff;
    --ink-soft: #f6f3f1;
  }
  * { box-sizing: border-box; margin: 0; padding: 0; }
  html, body { width: 1200px; height: 1015px; overflow: hidden; }
  body {
    background: var(--bg);
    font-family: "Exo 2", sans-serif;
    position: relative;
  }
  .card {
    position: absolute;
    left: 250px;
    width: 700px;
    height: 400px;
    overflow: hidden;
    background: var(--green);
    box-shadow: 0 12px 30px rgba(0,0,0,0.55);
  }
  .card--back { top: 75px; }
  .card--front { top: 545px; }

  .back-pattern {
    position: absolute; inset: 0;
    background: linear-gradient(135deg, var(--green) 0%, var(--green-deep) 50%, var(--green) 100%);
  }
  .back-mark {
    position: absolute;
    right: 70px; top: 150px;
    display: flex; align-items: center; gap: 10px;
    padding: 14px 18px;
    background: var(--green);
    border: 2px solid var(--white);
    border-radius: 10px;
  }
  .back-mark__square { width: 14px; height: 14px; background: var(--white); }
  .back-mark__name {
    color: var(--white); font-weight: 700; font-size: 16px;
    line-height: 1.1; text-transform: uppercase; letter-spacing: 0.5px;
  }

  .front-shapes { position: absolute; inset: 0; }
  .front-brand {
    position: absolute;
    left: 430px; top: 130px; width: 230px;
    text-align: center;
    color: var(--ink-soft); font-weight: 800;
    text-transform: uppercase; line-height: 1.1;
  }
  .front-brand__line1 { font-size: 34px; letter-spacing: 0.5px; }
  .front-brand__line2 { font-size: 22px; letter-spacing: 2px; margin-top: 6px; }
  .front-brand__square { width: 26px; height: 26px; background: var(--ink-soft); margin: 0 auto 14px; }

  .person { position: absolute; left: 48px; top: 118px; color: var(--white); }
  .person__name { font-weight: 800; font-size: 24px; letter-spacing: 0.5px; text-transform: uppercase; }
  .person__title { font-size: 16px; margin-top: 2px; }

  .contacts { position: absolute; left: 48px; top: 215px; list-style: none; color: var(--white); font-size: 16px; }
  .contacts li { display: flex; align-items: center; gap: 10px; height: 26px; }
  .contacts svg { width: 16px; height: 16px; flex: none; }

  .address { position: absolute; left: 48px; top: 315px; color: var(--white); font-size: 16px; line-height: 1.35; font-style: normal; }
</style>
</head>
<body>

<section class="card card--back" aria-label="Card back">
  <div class="back-pattern" role="img" aria-label="Repeating pattern of the company mark in a darker green tone"></div>
  <div class="back-mark">
    <span class="back-mark__square"></span>
    <span class="back-mark__name">Tallbrook<br>Construction</span>
  </div>
</section>

<section class="card card--front" aria-label="Card front">
  <svg class="front-shapes" viewBox="0 0 700 400" width="700" height="400" aria-hidden="true">
    <polygon points="400,0 700,0 700,400 400,400 340,330 340,70" fill="var(--white)"/>
    <polygon points="440,75 640,75 665,100 665,290 640,318 440,318 412,290 412,100" fill="var(--green)"/>
  </svg>

  <div class="front-brand">
    <div class="front-brand__square"></div>
    <div class="front-brand__line1">Tallbrook</div>
    <div class="front-brand__line2">Construction</div>
  </div>

  <div class="person">
    <h1 class="person__name">Marcus Hale</h1>
    <p class="person__title">Managing Director</p>
  </div>

  <ul class="contacts">
    <li>
      <svg viewBox="0 0 24 24" fill="none" stroke="currentColor" stroke-width="2"><path d="M5 3h4l2 5-3 2a12 12 0 0 0 6 6l2-3 5 2v4a2 2 0 0 1-2 2A18 18 0 0 1 3 5a2 2 0 0 1 2-2z"/></svg>
      044-555 018 273
    </li>
    <li>
      <svg viewBox="0 0 24 24" fill="none" stroke="currentColor" stroke-width="2"><rect x="2" y="5" width="20" height="14"/><path d="M2 5l10 8 10-8"/></svg>
      info@tallbrookbuild.com
    </li>
    <li>
      <svg viewBox="0 0 24 24" fill="none" stroke="currentColor" stroke-width="2"><circle cx="12" cy="12" r="10"/><path d="M2 12h20M12 2c3 3 3 17 0 20M12 2c-3 3-3 17 0 20"/></svg>
      www.tallbrookbuild.com
    </li>
  </ul>

  <address class="address">421, Address line goes here<br>45452, Country Name</address>
</section>

</body>
</html>
```